Business Cards Needed for Innovative Healthcare Marketing Company

We are a marketing company focused on healthcare. Our company is all about rebranding yourself renewing your image and generating results. The phoenix stands for "reborn" or "rising" which we provide new brands for our clients we take their old brands and renew it with creativity and innovation. I am looking for a business card with color dimension. I have attached an example of a card I think has the look and feel of what I am trying to accomplish. I like that the card example has black and grey font colors, I like the font placement and the small logo, I really like the use of the colors on the right those are the colors of my logo. My logo is phoenix so maybe incorporating flames similar to that design. I would like the back a solid color maybe red with an opaque version of the logo and website. As a marketing company I am always open to creative liberty!

Target Market(s)

Doctors and business professionals.

Industry/Entity Type

Marketing

Contact Information for Business Card

Valcorne Health Care Marketing
Marla Tenwick- CEO
#(512)638-2974
email-marla@valcorne.com
website- valcorne.com

Font styles to use
Sans Serif

Colors
ec1f27
f37122
ffc214
fbed22
fbf289
f04a50

Requirements
Must have
• The logo and required information
Nice to have
• icons by the information
Should not have
• child like font

```html
<!DOCTYPE html>
<html lang="en">
<head>
<meta charset="utf-8">
<title>Valcorne Health Care Marketing – Business Cards</title>
<link rel="stylesheet" href="https://fonts.googleapis.com/css2?family=Josefin+Sans:wght@300&family=Roboto+Slab:wght@400;700&display=swap">
<style>
  :root {
    --stage: #2a2320;
    --wine-light: #6e1a22;
    --wine-dark: #2c070b;
    --wine-mid: #4a0f15;
    --ink: #050505;
    --mark-dark: #1e1a1a;
    --mark-warm: #e8622a;
    --white: #f4f1ee;
    --grey: #c9c6c4;
    --accent-red: #e0323a;
    --accent-yellow: #ffc214;
  }
  * { margin: 0; padding: 0; box-sizing: border-box; }
  html, body { width: 1200px; height: 913px; overflow: hidden; }
  body {
    background: var(--stage);
    display: flex;
    align-items: center;
    justify-content: center;
    gap: 60px;
    font-family: "Roboto Slab", serif;
  }
  .card {
    position: relative;
    width: 520px;
    height: 297px;
    border-radius: 3px;
    overflow: hidden;
    box-shadow: 0 14px 30px rgba(0,0,0,.45);
  }

  /* Back of the card */
  .card--back {
    background: radial-gradient(ellipse at 62% 30%, var(--wine-light) 0%, var(--wine-mid) 55%, var(--wine-dark) 100%);
  }
  .back-mark {
    position: absolute;
    left: 40px;
    top: 72px;
    width: 150px;
    height: 150px;
    border-radius: 50%;
    background: var(--mark-dark);
  }
  .back-brand {
    position: absolute;
    left: 212px;
    top: 92px;
    width: 280px;
  }
  .back-brand__name {
    font-family: "Josefin Sans", sans-serif;
    font-weight: 300;
    font-size: 46px;
    letter-spacing: 1.5px;
    line-height: 1;
    color: var(--white);
  }
  .back-brand__rule {
    height: 1px;
    background: var(--grey);
    opacity: .7;
    margin: 7px 0 6px;
  }
  .back-brand__tagline {
    font-family: "Josefin Sans", sans-serif;
    font-weight: 300;
    font-size: 13px;
    letter-spacing: 1.4px;
    color: var(--grey);
  }
  .back-web {
    position: absolute;
    left: 250px;
    top: 196px;
    font-size: 18px;
    font-weight: 700;
    color: var(--grey);
  }
  .back-web__domain { color: var(--accent-red); }

  /* Front of the card */
  .card--front { background: var(--ink); }
  .front-shape { position: absolute; inset: 0; }
  .front-mark {
    position: absolute;
    left: 76px;
    top: 72px;
    width: 72px;
    height: 72px;
    border-radius: 50%;
    background: var(--mark-warm);
  }
  .front-brand {
    position: absolute;
    left: 32px;
    top: 156px;
    width: 160px;
    text-align: center;
  }
  .front-brand__name {
    font-family: "Josefin Sans", sans-serif;
    font-weight: 300;
    font-size: 27px;
    letter-spacing: 1px;
    line-height: 1;
    color: var(--accent-red);
  }
  .front-brand__tagline {
    font-family: "Josefin Sans", sans-serif;
    font-weight: 300;
    font-size: 7.5px;
    letter-spacing: .8px;
    color: var(--accent-red);
    margin-top: 4px;
    border-top: 1px solid rgba(224,50,58,.6);
    padding-top: 3px;
  }
  .contact {
    position: absolute;
    left: 285px;
    top: 70px;
    color: var(--grey);
  }
  .contact__name {
    font-size: 21px;
    font-weight: 700;
    color: var(--grey);
    line-height: 1.1;
  }
  .contact__name-last { text-transform: uppercase; }
  .contact__title { font-size: 15px; margin-bottom: 22px; }
  .contact__line {
    display: flex;
    align-items: center;
    gap: 9px;
    font-size: 14px;
    margin-bottom: 7px;
  }
  .contact__icon { width: 20px; height: 20px; flex: none; }
</style>
</head>
<body>

  <section class="card card--back" aria-label="Card back">
    <div class="back-mark" role="img" aria-label="Brand mark area"></div>
    <div class="back-brand">
      <div class="back-brand__name">VALCORNE</div>
      <div class="back-brand__rule"></div>
      <div class="back-brand__tagline">HEALTH CARE MARKETING</div>
    </div>
    <div class="back-web">www.<span class="back-web__domain">valcorne</span>.com</div>
  </section>

  <section class="card card--front" aria-label="Card front">
    <svg class="front-shape" viewBox="0 0 520 297" preserveAspectRatio="none" aria-hidden="true">
      <defs>
        <radialGradient id="wine-panel" cx="35%" cy="30%" r="80%">
          <stop offset="0" stop-color="#6e1a22"/>
          <stop offset=".6" stop-color="#4a0f15"/>
          <stop offset="1" stop-color="#2c070b"/>
        </radialGradient>
      </defs>
      <path d="M0 0 H150 C225 40 250 150 220 297 H0 Z" fill="url(#wine-panel)"/>
      <path d="M165 0 H200 C255 60 262 160 236 230 C245 150 225 60 165 0 Z" fill="#6e1a22"/>
    </svg>

    <div class="front-mark" role="img" aria-label="Brand mark area"></div>
    <div class="front-brand">
      <div class="front-brand__name">VALCORNE</div>
      <div class="front-brand__tagline">HEALTH CARE MARKETING</div>
    </div>

    <div class="contact">
      <div class="contact__name">Marla <span class="contact__name-last">Tenwick</span></div>
      <div class="contact__title">CEO</div>
      <div class="contact__line">
        <svg class="contact__icon" viewBox="0 0 20 20" aria-hidden="true">
          <circle cx="10" cy="10" r="10" fill="var(--accent-yellow)"/>
          <path d="M5 8 C7 13 9 14 13 15 L15 13 L12.5 11.5 L11.5 12.5 C10 12 8.5 10.5 8 9 L9 8 L7.5 5.5 Z" fill="#050505"/>
        </svg>
        <span>(512) 638-2974</span>
      </div>
      <div class="contact__line">
        <svg class="contact__icon" viewBox="0 0 20 20" aria-hidden="true">
          <circle cx="10" cy="10" r="10" fill="var(--accent-yellow)"/>
          <rect x="5" y="6.5" width="10" height="7" fill="#050505"/>
          <path d="M5 6.5 L10 10.5 L15 6.5" fill="none" stroke="#ffc214" stroke-width="1"/>
        </svg>
        <span>marla@valcorne.com</span>
      </div>
    </div>
  </section>

</body>
</html>
```